A clean crisp business card for a Landscape Construction company. Designed to be easy to read contact/ info and also be appealing/interesting, unlike a traditional business card.

Industry/Entity Type

Landscape Construction

Contact Information for Business Card

Company name : Brambleford Landscape Construction, phone number: (877) 62Vista, website:Bramblefordyards.example, Email, sales@bramblefordyards.example

Requirements
Nice to have
• Luxurious finishes/ details…. Icons or emblems next to contact info
Should not have
• Clipart or general pictures

```html
<!DOCTYPE html>
<html lang="en">
<head>
<meta charset="utf-8">
<title>Brambleford Landscape Construction – Business Card</title>
<link href="https://fonts.googleapis.com/css2?family=Source+Sans+3:wght@400;600&display=swap" rel="stylesheet">
<style>
  :root {
    --card: #231f20;
    --paper: #ffffff;
    --blue: #1f6db5;
    --green: #9dc843;
    --teal: #1ba6b8;
    --ink: #ffffff;
  }
  * { margin: 0; padding: 0; box-sizing: border-box; }
  html, body { width: 1200px; height: 391px; overflow: hidden; background: var(--paper); }
  body { position: relative; font-family: "Source Sans 3", sans-serif; color: var(--ink); }

  .card { position: absolute; top: 44px; height: 347px; background: var(--card); overflow: hidden; }
  .card-front { left: 0; width: 578px; }
  .card-back { left: 621px; width: 579px; }

  .brand { position: absolute; text-align: center; color: var(--green); font-weight: 600; }
  .brand-mark { display: block; margin: 0 auto 6px; border-radius: 50%; background: var(--blue); }
  .brand-name { display: block; line-height: 1; }
  .brand-sub { display: block; text-transform: uppercase; line-height: 1; }

  .card-front .brand { left: 38px; top: 148px; width: 240px; }
  .card-front .brand-mark { width: 26px; height: 26px; }
  .card-front .brand-name { font-size: 33px; }
  .card-front .brand-sub { font-size: 10.5px; letter-spacing: 3.2px; margin-top: 5px; }

  .card-back .brand { left: 126px; top: 112px; width: 320px; }
  .card-back .brand-mark { width: 40px; height: 40px; margin-bottom: 10px; }
  .card-back .brand-name { font-size: 48px; }
  .card-back .brand-sub { font-size: 14px; letter-spacing: 4.6px; margin-top: 8px; }

  .person { position: absolute; right: 47px; top: 76px; text-align: right; }
  .person-name { font-size: 19px; font-weight: 400; letter-spacing: 0.2px; line-height: 1; margin-right: 25px; }
  .person-title { font-size: 14px; color: var(--blue); line-height: 1; margin-top: 5px; }
  .person-rule { width: 53px; height: 1.5px; background: var(--teal); margin: 4px 0 0 auto; }

  .contacts { position: absolute; right: 47px; top: 150px; list-style: none; }
  .contact { display: flex; align-items: center; justify-content: flex-end; gap: 11px; font-size: 12.3px; line-height: 1.3; text-align: right; }
  .contact + .contact { margin-top: 9px; }
  .contact-address { margin-bottom: 6px; }
  .icon { flex: none; width: 17px; height: 17px; border-radius: 3px; background: var(--blue); display: flex; align-items: center; justify-content: center; }
  .icon svg { width: 11px; height: 11px; fill: #fff; }

  .bands { position: absolute; left: 0; bottom: 0; }
</style>
</head>
<body>
  <section class="card card-front">
    <div class="brand">
      <span class="brand-mark"></span>
      <span class="brand-name">Brambleford</span>
      <span class="brand-sub">Landscape Construction</span>
    </div>

    <div class="person">
      <p class="person-name">DANIEL R. ASHWORTH</p>
      <p class="person-title">Managing Director</p>
      <div class="person-rule"></div>
    </div>

    <ul class="contacts">
      <li class="contact contact-address">
        <span>4127 Meadowcrest Rd., Suite 210,<br>Elm Harbor, OH 45990</span>
        <span class="icon"><svg viewBox="0 0 12 12"><path d="M6 0a4 4 0 0 0-4 4c0 3 4 8 4 8s4-5 4-8a4 4 0 0 0-4-4zm0 5.6A1.6 1.6 0 1 1 6 2.4a1.6 1.6 0 0 1 0 3.2z"/></svg></span>
      </li>
      <li class="contact">
        <span>(877) 62Vista</span>
        <span class="icon"><svg viewBox="0 0 12 12"><path d="M2.5 0.5l2 2.2-1 1.4c.8 1.7 2 2.9 3.6 3.7l1.3-1 2.2 2-1.1 2.2C4.5 10.6 1.1 7 0.4 1.6z"/></svg></span>
      </li>
      <li class="contact">
        <span>sales@bramblefordyards.example</span>
        <span class="icon"><svg viewBox="0 0 12 12"><path d="M0 2h12v8H0zM1 3v.3l5 3.4 5-3.4V3zm0 1.5V9h10V4.5L6 8z"/></svg></span>
      </li>
      <li class="contact">
        <span>bramblefordyards.example</span>
        <span class="icon"><svg viewBox="0 0 12 12"><path d="M3 0l7 7H6.5l2 4.2-1.4.7-2-4.2L3 10z"/></svg></span>
      </li>
    </ul>

    <svg class="bands" width="578" height="42" viewBox="0 0 578 42" aria-hidden="true">
      <polygon points="19,5 302,5 281,27 19,27" fill="var(--blue)"/>
      <polygon points="310,5 559,5 559,27 290,27" fill="var(--green)"/>
    </svg>
  </section>

  <section class="card card-back">
    <svg width="579" height="347" viewBox="0 0 579 347" style="position:absolute;left:0;top:0" aria-hidden="true">
      <polygon points="0,81 39,102 39,244 0,265" fill="var(--green)"/>
      <polygon points="579,81 540,101 540,244 579,265" fill="var(--blue)"/>
    </svg>
    <div class="brand">
      <span class="brand-mark"></span>
      <span class="brand-name">Brambleford</span>
      <span class="brand-sub">Landscape Construction</span>
    </div>
  </section>
</body>
</html>
```